Seeking funky, innovative business cards

I am looking to refresh our current business cards to something more engaging, visual and impactful. We are a management consultancy firm, see website (www.larkstone-partners.com.au). I've included our colour scheme, sample of the slides we use and our old business cards. We would like our cards to have icons. The card should display:- Name- Title- Mobile number- Address- Email address- Website - Company logo- Our purpose statement "We create the best places on earth to work"

Contact Information for Business Card

Brennan Ulfsson
Consultant
0468 927 341
Level 3, 218 Wexley Street, Melbourne 3000
brennan@larkstone-partners.com.au
www.larkstone-partners.com.au

Purpose statement "we create the best places on earth to work"
LOGO available in google images

Font styles to use
Other font styles liked:
• Open Sans Light, Bebas Neue (open to other cool foints)

Colors
ffc214
5c5c5c
f5f5f5
fefefe

Requirements
Must have
• - Name
• - Title
• - Mobile number
• - Address
• - Email address
• - Website
• - Company logo
• - Our purpose statement "We create the best places on earth to work"
Nice to have
• - Icons
• - Colour (see our colour scheme"

```html
<!DOCTYPE html>
<html lang="en">
<head>
<meta charset="utf-8">
<title>Larkstone Partners – Business Card</title>
<link href="https://fonts.googleapis.com/css2?family=Lato:wght@300;400;700;900&family=Open+Sans:wght@400;600&display=swap" rel="stylesheet">
<style>
  :root{
    --backdrop:#d9d9d9;
    --card:#474a4b;
    --yellow:#f5c518;
    --orange:#f7a21b;
    --white:#fefefe;
    --soft:#f5f5f5;
  }
  *{box-sizing:border-box;margin:0;padding:0}
  html,body{width:1200px;height:900px;overflow:hidden}
  body{
    background:var(--backdrop);
    display:flex;flex-direction:column;align-items:center;justify-content:center;gap:34px;
    font-family:'Lato',sans-serif;color:var(--white);
  }
  .card{
    position:relative;width:700px;height:400px;background:var(--card);
    box-shadow:0 10px 24px rgba(0,0,0,.25);overflow:hidden;
  }
  .card::after{
    content:"";position:absolute;left:0;right:0;bottom:0;height:8px;background:var(--orange);
  }
  .card--contact::before{
    content:"";position:absolute;left:0;top:0;bottom:0;width:6px;background:var(--orange);
  }
  .brand{display:flex;align-items:center;gap:12px}
  .brand__dot{width:14px;height:14px;border-radius:50%;background:var(--yellow);flex:none}
  .brand__name{font-weight:300;color:var(--white);letter-spacing:.5px;white-space:nowrap}

  .card--contact .brand{position:absolute;right:52px;top:58px}
  .card--contact .brand__name{font-size:36px}

  .person{position:absolute;left:52px;top:178px}
  .person__name{font-weight:900;color:var(--yellow);font-size:25px;letter-spacing:1.5px;text-transform:uppercase}
  .person__title{font-size:16px;color:var(--soft);margin-top:2px}
  .divider{position:absolute;left:52px;right:52px;top:244px;height:1px;background:var(--yellow)}

  .contacts{position:absolute;left:52px;top:264px;list-style:none;font-size:16px;line-height:28px;color:var(--soft)}
  .contacts li{display:flex;align-items:center;gap:12px}
  .contacts svg{width:13px;height:13px;fill:var(--yellow);flex:none}

  .address{position:absolute;right:52px;top:300px;text-align:right;font-size:16px;line-height:24px;color:var(--soft);font-style:normal}

  .card--front{display:flex;flex-direction:column;align-items:center;justify-content:center}
  .card--front .brand__name{font-size:56px}
  .card--front .brand__dot{width:20px;height:20px}
  .purpose{
    position:absolute;bottom:42px;left:0;right:0;text-align:center;
    font-family:'Open Sans',sans-serif;font-weight:600;font-size:22px;color:var(--yellow);
  }
</style>
</head>
<body>

  <section class="card card--contact">
    <div class="brand">
      <span class="brand__dot"></span>
      <span class="brand__name">Larkstone Partners</span>
    </div>

    <div class="person">
      <h1 class="person__name">Brennan Ulfsson</h1>
      <p class="person__title">Consultant</p>
    </div>
    <div class="divider"></div>

    <ul class="contacts">
      <li>
        <svg viewBox="0 0 24 24" aria-hidden="true"><path d="M6.6 10.8a15.1 15.1 0 0 0 6.6 6.6l2.2-2.2c.3-.3.7-.4 1-.2 1.1.4 2.3.6 3.6.6.6 0 1 .4 1 1V20c0 .6-.4 1-1 1A17 17 0 0 1 3 4c0-.6.4-1 1-1h3.5c.6 0 1 .4 1 1 0 1.3.2 2.5.6 3.6.1.3 0 .7-.2 1z"/></svg>
        0468 927 341
      </li>
      <li>
        <svg viewBox="0 0 24 24" aria-hidden="true"><path d="M3 5h18v14H3zm2 2v.5l7 5 7-5V7zm0 3v7h14v-7l-7 5z"/></svg>
        brennan@larkstone-partners.com.au
      </li>
      <li>
        <svg viewBox="0 0 24 24" aria-hidden="true"><path d="M12 2a10 10 0 1 0 0 20 10 10 0 0 0 0-20zm0 2c.9 1.2 1.6 2.6 2 4h-4c.4-1.4 1.1-2.8 2-4zM4.3 14a8 8 0 0 1 0-4h3.4a16 16 0 0 0 0 4zm.8 2h3c.3 1.3.8 2.5 1.4 3.6A8 8 0 0 1 5.1 16zM8.1 8h-3a8 8 0 0 1 4.4-3.6C8.9 5.5 8.4 6.7 8.1 8zM12 20c-.9-1.2-1.6-2.6-2-4h4c-.4 1.4-1.1 2.8-2 4zm2.3-6H9.7a14 14 0 0 1 0-4h4.6a14 14 0 0 1 0 4zm.2 5.6c.6-1.1 1.1-2.300 1.4-3.6h3a8 8 0 0 1-4.4 3.6zm1.8-5.6a16 16 0 0 0 0-4h3.4a8 8 0 0 1 0 4zM15.9 8c-.3-1.3-.8-2.5-1.4-3.6A8 8 0 0 1 18.9 8z"/></svg>
        www.larkstone-partners.com.au
      </li>
    </ul>

    <address class="address">
      Level 3, 218 Wexley Street<br>
      Melbourne 3000
    </address>
  </section>

  <section class="card card--front">
    <div class="brand">
      <span class="brand__dot"></span>
      <span class="brand__name">Larkstone Partners</span>
    </div>
    <p class="purpose">We create the best places on earth to work</p>
  </section>

</body>
</html>
```